Healthcare and Professional IT Services Company need a redesigned business card

We are a IT Services company that targets small medical practices and professional business such as Attorneys, Accounts, Architects etc. We want to communicate a professional yet friendly image using recent logo redesign here on ArtHarbor. Like to see the colors blue and orange in the design. Must use the Tall Pine Computing as displayed in the new logo - then also want to incorporate the fish logo as well.

Target Market(s)

Small medical and professional services

Industry/Entity Type

It Company

Contact Information for Business Card

The usual stuff, place for name address phone website. Also maybe our tagline which is "hooked on technology"

Requirements
Must have
• My new logo and the fish somewhere on the card

```html
<!DOCTYPE html>
<html lang="en">
<head>
<meta charset="UTF-8">
<title>Tall Pine Computing – Business Card</title>
<link href="https://fonts.googleapis.com/css2?family=Open+Sans:wght@300;400;600&display=swap" rel="stylesheet">
<style>
  :root {
    --stage: #e9e9ea;
    --paper: #ffffff;
    --paper-shade: #f1f2f3;
    --band-blue: #1a8fcb;
    --band-blue-deep: #0f74b0;
    --accent-orange: #f2a51c;
    --brand-blue: #4eb3ea;
    --name-blue: #5aaee0;
    --ink: #2b2b2b;
    --fish-teal: #3fb8c8;
    --fish-orange: #e89a62;
  }
  * { margin: 0; padding: 0; box-sizing: border-box; }
  html, body {
    width: 1200px; height: 892px; overflow: hidden;
    background: var(--stage);
    font-family: "Open Sans", Arial, sans-serif;
  }
  .canvas {
    width: 1200px; height: 892px;
    display: flex; align-items: center; justify-content: center; gap: 40px;
  }
  .card {
    position: relative;
    width: 540px; height: 310px;
    background: linear-gradient(160deg, var(--paper) 60%, var(--paper-shade));
    box-shadow: 0 10px 26px rgba(0,0,0,0.18);
    overflow: hidden;
  }
  /* Front */
  .band {
    position: absolute; left: 0; right: 0; height: 30px;
    background: linear-gradient(90deg, var(--band-blue-deep), var(--band-blue));
  }
  .band--top { top: 0; border-bottom: 4px solid var(--paper); }
  .band--bottom { bottom: 0; border-top: 4px solid var(--paper); }
  .rule {
    position: absolute; left: 0; right: 0; height: 4px; background: var(--accent-orange);
  }
  .rule--top { top: 34px; }
  .rule--bottom { bottom: 34px; }
  .mascot {
    position: absolute; left: 30px; top: 82px; width: 120px; height: 100px;
    border-radius: 50% 45% 40% 50%;
    background: radial-gradient(circle at 55% 45%, var(--fish-teal), var(--fish-orange) 95%);
    opacity: 0.85;
  }
  .brand {
    position: absolute; left: 170px; top: 68px;
    font-weight: 600; font-size: 34px; line-height: 1.05;
    color: var(--brand-blue); letter-spacing: -0.5px;
  }
  .holder-name {
    position: absolute; left: 170px; top: 146px;
    font-weight: 300; font-size: 26px; color: var(--name-blue);
  }
  .contacts {
    position: absolute; left: 170px; top: 186px; list-style: none;
    font-size: 14px; color: var(--ink);
  }
  .contacts li { display: flex; align-items: center; gap: 10px; height: 23px; }
  .contacts svg { width: 15px; height: 15px; flex: none; }
  /* Back */
  .card--back { display: flex; flex-direction: column; align-items: center; justify-content: center; }
  .back-mark {
    display: flex; align-items: center; gap: 14px;
  }
  .back-mark .dot {
    width: 22px; height: 22px; border-radius: 50%; background: var(--accent-orange);
  }
  .back-brand {
    font-weight: 600; font-size: 40px; color: var(--brand-blue); letter-spacing: -0.5px;
  }
</style>
</head>
<body>
<main class="canvas">
  <section class="card card--front">
    <div class="band band--top"></div>
    <div class="rule rule--top"></div>
    <div class="mascot" role="img" aria-label="Cartoon fish mascot illustration"></div>
    <div class="brand">Tall Pine<br>Computing</div>
    <div class="holder-name">Daniel Merrow</div>
    <ul class="contacts">
      <li>
        <svg viewBox="0 0 16 16"><rect width="16" height="16" rx="2" fill="#f2a51c"/><path d="M5 4c1 0 1.5 1.6 1 2.2-.4.4.2 1.5 1.6 2.8 1.3 1.2 2.2 1.6 2.6 1.2.6-.6 2 0 2 .9 0 .8-1 1.5-2 1.3C7.6 11.8 4.4 8.6 4 6 3.8 5 4.3 4 5 4z" fill="#fff"/></svg>
        +94 5210 7788
      </li>
      <li>
        <svg viewBox="0 0 16 16"><rect width="16" height="16" rx="2" fill="#f2a51c"/><circle cx="8" cy="8" r="4.5" fill="none" stroke="#fff" stroke-width="1.3"/><path d="M3.5 8h9M8 3.5c-2 2.5-2 6.5 0 9M8 3.5c2 2.5 2 6.5 0 9" fill="none" stroke="#fff" stroke-width="1"/></svg>
        www.tallpinecomputing.com
      </li>
      <li>
        <svg viewBox="0 0 16 16"><rect width="16" height="16" rx="2" fill="#f2a51c"/><path d="M8 3a3 3 0 0 1 3 3c0 2.3-3 6.5-3 6.5S5 8.3 5 6a3 3 0 0 1 3-3z" fill="#fff"/><circle cx="8" cy="6" r="1.1" fill="#f2a51c"/></svg>
        4820 Cedar Ave, Ridgeview, BC
      </li>
    </ul>
    <div class="rule rule--bottom"></div>
    <div class="band band--bottom"></div>
  </section>

  <section class="card card--back">
    <div class="back-mark">
      <span class="dot"></span>
      <span class="back-brand">Tall Pine Computing</span>
    </div>
  </section>
</main>
</body>
</html>
```